We need a flyer designed for our 4th Annual Harvestlight: A Kinfolk Homecoming for the Heritage Festival that includes the day, time, location, address, and logos. It also needs to include what to expect. The event will be held on Saturday June 14th from 12p-6p at Cedar Commons located at 417 N. Bellmora St., Pensacola, FL 32507. Please see uploaded files for prior flyers for reference when it comes to information to include. Also I've uploaded pictures from our prior festivals that you may incorporate and logos.

```html
<!DOCTYPE html>
<html lang="en">
<head>
<meta charset="utf-8">
<title>Harvestlight – A Kinfolk Homecoming for the Heritage Festival</title>
<link rel="stylesheet" href="https://fonts.googleapis.com/css2?family=Anton&family=Open+Sans:wght@700;800&display=swap">
<style>
  :root{
    --green:#7ab53a;
    --red:#e31e25;
    --yellow:#fdee00;
    --blue:#27a7df;
    --magenta:#e6097f;
    --orange:#f47a20;
    --purple:#6b2a8c;
    --ink:#000;
    --paper:#fff;
    --gold:#e0a526;
    --pill:#c9c9c9;
  }
  html,body{margin:0;padding:0;overflow:hidden;background:#222;}
  .flyer{
    position:relative;width:927px;height:1200px;overflow:hidden;
    font-family:"Open Sans",Arial,sans-serif;
    background:
      conic-gradient(from 200deg at 52% 42%,
        var(--yellow) 0deg, var(--orange) 40deg, var(--red) 80deg,
        var(--magenta) 120deg, var(--purple) 160deg, var(--blue) 200deg,
        #12a89b 230deg, var(--green) 260deg, var(--yellow) 300deg,
        #f7b21b 330deg, var(--yellow) 360deg);
  }
  .abs{position:absolute;}
  .host{left:300px;top:92px;display:flex;align-items:center;gap:14px;}
  .host-dot{width:62px;height:62px;border-radius:50%;background:var(--ink);}
  .host-name{font-weight:800;font-size:30px;color:var(--ink);line-height:1.05;width:420px;}
  .presents{left:0;width:927px;padding-left:370px;box-sizing:border-box;top:168px;text-align:center;font-weight:800;font-size:27px;color:var(--ink);}
  .annual{left:533px;top:212px;font-weight:800;font-size:38px;line-height:1.1;color:var(--ink);z-index:2;}
  .annual sup{font-size:22px;}
  .photo{border-radius:50%;border:2px solid rgba(255,255,255,.7);}
  .title-art{left:0;top:0;z-index:1;}
  .tagline{left:159px;top:695px;width:614px;height:43px;border-radius:22px;background:var(--ink);z-index:2;
    color:var(--yellow);font-weight:700;font-size:24.5px;display:flex;align-items:center;justify-content:center;white-space:nowrap;}
  .crowd{left:0;top:740px;width:927px;height:460px;
    background:linear-gradient(to bottom,rgba(0,0,0,0) 0%,rgba(0,0,0,.85) 22%,var(--ink) 40%);}
  .date{left:150px;top:884px;width:360px;text-align:center;}
  .date-day{font-weight:800;font-size:40px;color:var(--paper);line-height:1;}
  .date-main{font-family:"Anton",Impact,sans-serif;font-size:84px;color:var(--yellow);line-height:1.05;}
  .date-main sup{font-size:46px;vertical-align:28px;}
  .date-time{font-weight:800;font-size:34px;color:var(--paper);line-height:1.1;}
  .venue{left:555px;top:930px;width:303px;height:90px;border-radius:45px;background:var(--pill);
    display:flex;align-items:center;gap:10px;padding-left:18px;box-sizing:border-box;}
  .venue-name{font-weight:800;font-size:24px;color:var(--ink);line-height:1.05;}
  .venue-addr{font-weight:700;font-size:16.5px;color:var(--ink);line-height:1.25;}
  .features{left:40px;top:1072px;width:550px;text-align:center;color:var(--gold);
    font-weight:800;font-size:18px;line-height:25px;text-transform:uppercase;}
  .divider{left:593px;top:1063px;width:1px;height:108px;background:#444;}
  .sponsor{left:636px;top:1110px;display:flex;align-items:center;gap:10px;}
  .sponsor-mark{width:34px;height:34px;background:var(--gold);}
  .sponsor-name{font-weight:700;font-size:17px;color:var(--paper);}
</style>
</head>
<body>
<main class="flyer">

  <div class="abs host">
    <span class="host-dot"></span>
    <span class="host-name">The Okafor Family Foundation</span>
  </div>
  <div class="abs presents">PRESENTS</div>
  <div class="abs annual">4<sup>th</sup> Annual</div>

  <div class="abs photo" style="left:90px;top:217px;width:104px;height:104px;background:radial-gradient(circle,#f2f2ee,#4f8f3a);" role="img" aria-label="Photo of festival hosts speaking on stage"></div>
  <div class="abs photo" style="left:28px;top:306px;width:166px;height:166px;background:radial-gradient(circle,#3a3a3a,#6f9a3f);" role="img" aria-label="Photo of dancers performing on the lawn"></div>
  <div class="abs photo" style="left:-12px;top:485px;width:210px;height:210px;background:radial-gradient(circle,#c0602a,#4a4a5a);" role="img" aria-label="Photo of cooks grilling at the festival"></div>
  <div class="abs photo" style="left:720px;top:253px;width:192px;height:192px;background:radial-gradient(circle,#7a4aa0,#6f8f4a);" role="img" aria-label="Photo of a step team performing"></div>
  <div class="abs photo" style="left:757px;top:414px;width:148px;height:148px;background:radial-gradient(circle,#d8d8d8,#3a6aa8);" role="img" aria-label="Photo of performers singing on stage"></div>
  <div class="abs photo" style="left:757px;top:553px;width:154px;height:154px;background:radial-gradient(circle,#6a7a4a,#2a2a2a);" role="img" aria-label="Photo of drummers in traditional attire"></div>

  <svg class="abs title-art" width="927" height="700" viewBox="0 0 927 700" aria-label="Harvestlight">
    <g font-family="Anton, Impact, sans-serif">
      <text x="185" y="514" font-size="277" textLength="559" lengthAdjust="spacingAndGlyphs" fill="#000">HARVEST</text>
      <text x="179" y="509" font-size="277" textLength="559" lengthAdjust="spacingAndGlyphs" stroke="#fff" stroke-width="3" paint-order="stroke">
        <tspan fill="#7ab53a">H</tspan><tspan fill="#e31e25">A</tspan><tspan fill="#fdee00">R</tspan><tspan fill="#27a7df">V</tspan><tspan fill="#e6097f">E</tspan><tspan fill="#7ab53a">S</tspan><tspan fill="#e31e25">T</tspan>
      </text>
      <text x="161" y="691" font-size="192" textLength="590" lengthAdjust="spacingAndGlyphs" fill="#000">LIGHT</text>
      <text x="155" y="686" font-size="192" textLength="590" lengthAdjust="spacingAndGlyphs" stroke="#fff" stroke-width="3" paint-order="stroke">
        <tspan fill="#fdee00">L</tspan><tspan fill="#e31e25">I</tspan><tspan fill="#7ab53a">G</tspan><tspan fill="#e6097f">H</tspan><tspan fill="#27a7df">T</tspan>
      </text>
    </g>
  </svg>

  <div class="abs tagline">A Kinfolk Homecoming for the Heritage Festival</div>

  <div class="abs crowd" role="img" aria-label="Silhouettes of a cheering crowd with raised hands"></div>

  <div class="abs date">
    <div class="date-day">SATURDAY</div>
    <div class="date-main">June 14<sup>th</sup></div>
    <div class="date-time">12PM-6PM</div>
  </div>

  <div class="abs venue">
    <svg width="26" height="40" viewBox="0 0 26 40" aria-hidden="true">
      <path d="M13 1C6.4 1 1 6.2 1 12.8 1 21 13 39 13 39S25 21 25 12.8C25 6.2 19.6 1 13 1Zm0 17a5.5 5.5 0 1 1 0-11 5.5 5.5 0 0 1 0 11Z" fill="#000"/>
    </svg>
    <div>
      <div class="venue-name">CEDAR COMMONS</div>
      <div class="venue-addr">417 N. Bellmora St.,<br>Pensacola, FL 32507.</div>
    </div>
  </div>

  <div class="abs features">
    Live Performances | Food Vendors |<br>
    Art/African Clothing | Kids Obstacle Course &amp;<br>
    Play Area | Spades &amp; Domino Tables |<br>
    Bring Your Own Chairs or Picnic Blankets
  </div>

  <div class="abs divider"></div>

  <div class="abs sponsor">
    <span class="sponsor-mark"></span>
    <span class="sponsor-name">The Okafor Firm, PLLC</span>
  </div>

</main>
</body>
</html>
```